Real Estate Flyer

Hi - I am assisting a relative to sell a unit. I am looking to have a two page flyer designed (configured as a single page with back to back printing). I have uploaded two samples to give you an idea of the look and feel - one which relates to this property when originally purchased, the other for a different property.
The flyer should includes several key photos on the front along with the wording. The rear should include any secondary photos along with the floor plan.
The flyer should be close to A4 size.

Updates
Hi,
Industry/Entity Type
Real Estate
Look and feel
Each slider illustrates characteristics of the customer's brand and the style your logo design should communicate.

```html
<!DOCTYPE html>
<html lang="en">
<head>
<meta charset="utf-8">
<title>Oversized apartment in a lifestyle location</title>
<link href="https://fonts.googleapis.com/css2?family=Open+Sans:wght@400;600;700&display=swap" rel="stylesheet">
<style>
:root{
  --teal-top:#34bcc6;
  --teal-top-dark:#1d9fab;
  --teal:#1896a1;
  --teal-deep:#0d7883;
  --bar:rgba(10,80,90,.82);
  --ink:#0f2326;
  --white:#ffffff;
  --tick:#7fd24a;
}
*{margin:0;padding:0;box-sizing:border-box}
html,body{width:849px;height:1200px;overflow:hidden;background:#fff}
body{font-family:"Open Sans",Arial,sans-serif;color:var(--ink)}
.flyer{position:relative;width:849px;height:1200px;overflow:hidden;
  background:linear-gradient(180deg,var(--teal) 0%,var(--teal-deep) 100%)}
.header{position:absolute;top:0;left:0;width:849px;height:155px;
  background:linear-gradient(180deg,var(--teal-top) 0%,var(--teal-top-dark) 100%);padding:22px 30px 0}
.title{color:var(--white);font-weight:700;font-size:38px;letter-spacing:-.3px;line-height:1.1}
.specs{position:absolute;right:30px;top:104px;color:var(--white);font-weight:600;font-size:19px;letter-spacing:.5px}
.photo{position:absolute;top:155px;left:0;width:849px;height:590px;
  background:linear-gradient(160deg,#c9a98c 0%,#e8dccb 35%,#9fb9c9 65%,#4d88b8 100%)}
.inspect{position:absolute;top:693px;left:0;width:849px;height:50px;background:var(--bar);
  color:var(--white);font-size:22px;font-weight:600;display:flex;align-items:center;padding-left:120px;gap:60px}
.address{position:absolute;top:758px;left:0;width:849px;text-align:center;font-size:25px;font-weight:700;color:var(--ink)}
.intro{position:absolute;top:806px;left:30px;width:790px;font-size:15px;line-height:1.45}
.features{position:absolute;top:920px;left:40px;width:780px;display:grid;grid-template-columns:1fr 1fr;row-gap:18px;column-gap:30px;list-style:none}
.features li{display:flex;align-items:flex-start;gap:10px;font-size:15px;line-height:1.3}
.features svg{flex:none;margin-top:2px}
.rates{position:absolute;top:1052px;left:30px;font-size:15px;line-height:1.4;border-collapse:collapse}
.rates td{padding:0 14px 0 0;vertical-align:top}
.contact{position:absolute;top:1060px;left:520px;width:300px;text-align:center}
.contact-name{font-size:28px;font-weight:600}
.contact-role{font-size:15px}
.contact-phone{font-size:32px;font-weight:700;margin-top:4px}
</style>
</head>
<body>
<div class="flyer">
  <header class="header">
    <h1 class="title">Oversized apartment in a lifestyle location</h1>
    <div class="specs">2 BED | 1 BATH | 1 CAR</div>
  </header>

  <div class="photo" role="img" aria-label="Photo of the apartment's large balcony terrace with living room and district views"></div>

  <div class="inspect">
    <span>Inspect :&nbsp;&nbsp;&nbsp;Sat 10:45 – 11:30</span>
    <span>Wed 12:00 – 12:30</span>
  </div>

  <h2 class="address">8/42-48 Harbour Lane, ELMWOOD HEIGHTS</h2>

  <p class="intro">Peacefully positioned on the 5th floor of a refurbished security building, this superbly spacious residence combines modern, low maintenance apartment living with inviting prospects for the entertainer. Boasting a huge full width terrace on-title, its sought after setting in the heart of Elmwood Heights offers the ultimate in lifestyle and convenience.</p>

  <ul class="features">
    <li><svg width="18" height="18" viewBox="0 0 18 18"><path d="M2 9l5 5 9-11" fill="none" stroke="var(--tick)" stroke-width="3"/></svg>Expansive open plan living and dining area</li>
    <li><svg width="18" height="18" viewBox="0 0 18 18"><path d="M2 9l5 5 9-11" fill="none" stroke="var(--tick)" stroke-width="3"/></svg>Built-ins in both bedrooms, fully tiled bathrooms</li>
    <li><svg width="18" height="18" viewBox="0 0 18 18"><path d="M2 9l5 5 9-11" fill="none" stroke="var(--tick)" stroke-width="3"/></svg>Terrace features city and Southern Bay glimpses</li>
    <li><svg width="18" height="18" viewBox="0 0 18 18"><path d="M2 9l5 5 9-11" fill="none" stroke="var(--tick)" stroke-width="3"/></svg>Internal laundry, secure parking, lift, outdoor pool and gymnasium</li>
    <li><svg width="18" height="18" viewBox="0 0 18 18"><path d="M2 9l5 5 9-11" fill="none" stroke="var(--tick)" stroke-width="3"/></svg>Kitchen updated with Norvel gas appliances</li>
    <li><svg width="18" height="18" viewBox="0 0 18 18"><path d="M2 9l5 5 9-11" fill="none" stroke="var(--tick)" stroke-width="3"/></svg>Steps to station, Elmwood Plaza and Ridgeway Park</li>
  </ul>

  <table class="rates">
    <tr><td>Water Rates:</td><td>To be provided on finalising design</td></tr>
    <tr><td>Council Rates:</td><td>To be provided on finalising design</td></tr>
    <tr><td>Strata Rates:</td><td>To be provided on finalising design</td></tr>
    <tr><td>(Estimated)</td><td></td></tr>
    <tr><td>Market Rental:</td><td>$700.00 p/w</td></tr>
  </table>

  <div class="contact">
    <div class="contact-name">Contact:&nbsp;&nbsp;Daniel Morrow</div>
    <div class="contact-role">(Assisting owner in Private Sale)</div>
    <div class="contact-phone">0400 123 456</div>
  </div>
</div>
</body>
</html>
```